Business Card Design

Hi I need a business card designed, we already have the business name logo artwork and would like some concept ideas for the Bus Card layout.
On the back of the card i want to include the products and services that we offer.
We are a Plastics Sheeting manufacture based in Perth Australia.

                                       

We need a BC design for a company called Tarvo Plastics based in Perth Australia.

We supply from DIY to Trade & Industrial  Engineering Markets.

We specialise in:

·         Cut to size panels  (all shapes and sizes)

·         Plastics fabrication & Welding

·         Custom Designs

·         Plastic Repairs

·         PVC Pipe Slotting & PVC Pipe Threading

·         Supplier of all types of engineering plastics and profiles.

Including:           Acrylic / Clarvene

                               Polycarbonate / Dorvil

                               Prismatic Light Diffuser

                               Vantrib

                               HDPE / UHMWPE

                               PVC / PVC Foam

                               Nylon

                               HIPS

```html
<!DOCTYPE html>
<html lang="en">
<head>
<meta charset="utf-8">
<title>Tarvo Plastics — Business Card</title>
<link href="https://fonts.googleapis.com/css2?family=Open+Sans:ital,wght@0,400;0,600;0,700;1,700&display=swap" rel="stylesheet">
<style>
  :root {
    --navy: #1c2a5a;
    --orange: #e8801f;
    --gold: #f2a81d;
    --white: #ffffff;
    --stage: #e4e5ea;
    --rule: #8e97b8;
  }
  * { box-sizing: border-box; margin: 0; padding: 0; }
  html, body { width: 1200px; height: 987px; overflow: hidden; }
  body {
    background: var(--stage);
    font-family: "Open Sans", Arial, sans-serif;
    display: flex; flex-direction: column; align-items: center; justify-content: center;
    gap: 44px;
  }
  .card {
    position: relative;
    width: 690px; height: 420px;
    border-radius: 22px;
    overflow: hidden;
    box-shadow: 0 10px 26px rgba(20, 25, 50, .18);
  }

  /* Front */
  .card-front { background: var(--white); }
  .front-brand {
    position: absolute; top: 26px; left: 0; right: 0;
    text-align: center;
    font-size: 62px; font-weight: 700; color: var(--navy);
    letter-spacing: -1px; line-height: 1;
  }
  .front-brand .brand-dot {
    display: inline-block; width: 18px; height: 18px;
    background: var(--orange); margin-right: 14px; vertical-align: middle;
  }
  .front-rule { position: absolute; left: 0; right: 0; height: 3px; background: var(--orange); }
  .front-rule.top { top: 112px; }
  .front-rule.bottom { top: 336px; }
  .front-band {
    position: absolute; left: 0; right: 0; top: 120px; height: 208px;
    background: var(--navy); color: var(--white);
    display: flex; align-items: center;
  }
  .address {
    width: 340px; padding-right: 34px;
    text-align: right; font-size: 18px; line-height: 1.42;
  }
  .band-divider { width: 1px; height: 150px; background: var(--rule); }
  .contacts { list-style: none; padding-left: 30px; font-size: 19px; line-height: 1.9; }
  .contacts li { display: flex; align-items: center; gap: 12px; }
  .contacts svg { width: 18px; height: 18px; fill: var(--white); flex: none; }
  .person {
    position: absolute; left: 52px; top: 356px;
    font-size: 25px; color: var(--navy); font-weight: 700;
  }
  .person .role { font-weight: 400; color: var(--orange); }

  /* Back */
  .card-back { background: var(--navy); color: var(--white); padding: 26px 40px; }
  .back-brand {
    text-align: right; font-size: 50px; font-weight: 700; line-height: 1; letter-spacing: -1px;
  }
  .tagline {
    margin-top: 14px; text-align: center;
    font-style: italic; font-weight: 700; font-size: 17px; line-height: 1.3;
  }
  .offer { display: flex; margin-top: 16px; }
  .offer-col { flex: 1; }
  .offer-col.products { flex: 0 0 238px; padding-left: 26px; }
  .offer-divider { width: 1px; background: var(--rule); margin: 24px 0 6px; }
  .offer h2 { color: var(--gold); font-size: 21px; font-weight: 700; line-height: 1.2; margin-bottom: 4px; }
  .offer ul { list-style: none; font-size: 15.5px; line-height: 1.36; }
  .offer li { padding-left: 14px; position: relative; }
  .offer li::before {
    content: ""; position: absolute; left: 0; top: 8px;
    width: 7px; height: 7px; border-radius: 50%; background: var(--gold);
  }
  .offer li .pair { margin-left: 10px; }
  .offer li .pair::before {
    content: ""; display: inline-block; width: 7px; height: 7px; border-radius: 50%;
    background: var(--gold); margin-right: 6px; vertical-align: middle;
  }
</style>
</head>
<body>

<section class="card card-front" aria-label="Business card front">
  <div class="front-brand"><span class="brand-dot"></span>Tarvo Plastics</div>
  <div class="front-rule top"></div>
  <div class="front-band">
    <address class="address" style="font-style:normal">
      Unit 4/18 Merrow Crescent<br>
      Kelvin Park WA 6112<br>
      PO Box 2270<br>
      Kelvin Park DC WA 6971<br>
      Halden Group Pty Ltd<br>
      T/A Tarvo Plastics ABN: TBA
    </address>
    <div class="band-divider"></div>
    <ul class="contacts">
      <li><svg viewBox="0 0 24 24" aria-hidden="true"><path d="M6.6 10.8a15 15 0 0 0 6.6 6.6l2.2-2.2c.3-.3.7-.4 1-.2 1.1.4 2.3.6 3.6.6.6 0 1 .4 1 1V20c0 .6-.4 1-1 1A17 17 0 0 1 3 4c0-.6.4-1 1-1h3.5c.6 0 1 .4 1 1 0 1.3.2 2.5.6 3.6.1.3 0 .7-.2 1z"/></svg>08 9000 4821</li>
      <li><svg viewBox="0 0 24 24" aria-hidden="true"><path d="M7 1h10a2 2 0 0 1 2 2v18a2 2 0 0 1-2 2H7a2 2 0 0 1-2-2V3a2 2 0 0 1 2-2zm0 3v14h10V4zm5 15.5a1.2 1.2 0 1 0 0 2.4 1.2 1.2 0 0 0 0-2.4z"/></svg>0400 000 123</li>
      <li><svg viewBox="0 0 24 24" aria-hidden="true"><path d="M6 2h9l3 3v5h1a3 3 0 0 1 3 3v6a2 2 0 0 1-2 2H4a2 2 0 0 1-2-2v-6a3 3 0 0 1 3-3h1zm2 2v6h8V6h-2V4zm-2 10v2h12v-2z"/></svg>08 9000 4822</li>
      <li><svg viewBox="0 0 24 24" aria-hidden="true"><path d="M2 5h20v14H2zm2 2v.4l8 5.2 8-5.2V7zm0 2.8V17h16V9.8l-8 5.2z"/></svg>sales@tarvoplastics.com.au</li>
    </ul>
  </div>
  <div class="front-rule bottom"></div>
  <p class="person">Your Name, <span class="role">Title</span></p>
</section>

<section class="card card-back" aria-label="Business card back">
  <div class="back-brand">Tarvo Plastics</div>
  <p class="tagline">The Products And Services That We Offer<br>Are Supplied From Diy To Trade &amp; Industrial Engineering Markets</p>
  <div class="offer">
    <div class="offer-col services">
      <h2>We specialise in:</h2>
      <ul>
        <li>Cut to size panels (all shapes and sizes)</li>
        <li>Plastics fabrication &amp; Welding</li>
        <li>Custom Designs</li>
        <li>Plastic Repairs</li>
        <li>PVC Pipe Slotting &amp; PVC Pipe Threading</li>
        <li>Supplier of all types of engineering plastics and profiles</li>
      </ul>
    </div>
    <div class="offer-divider"></div>
    <div class="offer-col products">
      <h2>Including:</h2>
      <ul>
        <li>Acrylic / Clarvene</li>
        <li>Polycarbonate / Dorvil</li>
        <li>Prismatic Light Diffuser</li>
        <li>Vantrib <span class="pair">HDPE / UHMWPE</span></li>
        <li>PVC / PVC Foam</li>
        <li>Nylon <span class="pair">HIPS</span></li>
      </ul>
    </div>
  </div>
</section>

</body>
</html>
```